Heron Loan Partners Business Card

We need a business card design for our mortgage servicing company. In addition to servicing the loans of homeowners, we help homeowners with purchasing their homes and any mortgage refinancing. We would like to see designs that use the colors in the logo attached below (gold-ish yellow and navy blue), and any other design you deem fit! The design should communicate a simpler life with smart mortgages provided by Heron.

```html
<!DOCTYPE html>
<html lang="en">
<head>
<meta charset="utf-8">
<title>Heron Loan Partners – Business Card</title>
<link rel="stylesheet" href="https://fonts.googleapis.com/css2?family=Montserrat:wght@400;500;700&display=swap">
<style>
  :root {
    --navy: #28214f;
    --gold: #dfb23f;
    --white: #ffffff;
    --stage: #1d1d1f;
  }
  * { box-sizing: border-box; margin: 0; padding: 0; }
  html, body {
    width: 1200px; height: 1015px; overflow: hidden;
    background: var(--stage);
    font-family: "Montserrat", Arial, sans-serif;
  }
  .card {
    position: absolute; left: 300px;
    width: 600px; height: 343px;
    overflow: hidden;
    box-shadow: 0 10px 30px rgba(0,0,0,.55);
  }
  .card--front { top: 110px; background: var(--navy); }
  .card--back { top: 545px; background: var(--white); }

  .band {
    position: absolute; left: 0; width: 100%;
    background: var(--gold);
    display: flex; align-items: center; justify-content: center;
    font-size: 17px; letter-spacing: 2px; font-weight: 500;
  }
  .card--front .band { top: 236px; height: 46px; color: var(--white); }

  .brand {
    position: absolute; display: flex; align-items: center; gap: 10px;
    color: var(--gold); font-weight: 700; white-space: nowrap;
  }
  .brand__dot {
    width: 14px; height: 14px; border-radius: 50%; background: var(--gold);
  }
  .card--front .brand { left: 0; width: 100%; top: 115px; justify-content: center; font-size: 34px; }

  .back__panel {
    position: absolute; top: 0; right: 0; width: 55%; height: 100%;
    background: var(--navy);
  }
  .card--back .brand { left: 0; width: 45%; top: 90px; justify-content: center; font-size: 22px; flex-direction: column; gap: 8px; text-align: center; line-height: 1.15; }
  .card--back .band { top: 218px; height: 40px; color: var(--navy); justify-content: flex-end; padding-right: 40px; }

  .contact {
    position: absolute; left: 48%; top: 36px; color: var(--white);
    font-size: 15px; line-height: 1.35;
  }
  .contact__name { color: var(--gold); font-weight: 700; font-size: 21px; letter-spacing: .5px; text-transform: uppercase; }
  .contact__role { margin-bottom: 12px; }
  .contact__row { display: flex; align-items: center; gap: 8px; }
  .contact__row svg { width: 15px; height: 15px; flex: none; }
  .contact__address { margin-top: 10px; padding-left: 23px; }
</style>
</head>
<body>

<section class="card card--front">
  <div class="brand"><span class="brand__dot"></span>Heron Loan Partners</div>
  <div class="band">www.heronloans.com</div>
</section>

<section class="card card--back">
  <div class="back__panel"></div>
  <div class="brand"><span class="brand__dot"></span>Heron Loan<br>Partners</div>

  <div class="contact">
    <p class="contact__name">Daniel Carter</p>
    <p class="contact__role">Managing Director</p>
    <p class="contact__row">
      <svg viewBox="0 0 24 24" aria-hidden="true"><path fill="var(--gold)" d="M6.6 10.8a15 15 0 0 0 6.6 6.6l2.2-2.2a1 1 0 0 1 1-.25 11.4 11.4 0 0 0 3.6.57 1 1 0 0 1 1 1V20a1 1 0 0 1-1 1A17 17 0 0 1 3 4a1 1 0 0 1 1-1h3.5a1 1 0 0 1 1 1c0 1.25.2 2.45.57 3.57a1 1 0 0 1-.25 1z"/></svg>
      044-987 654 321
    </p>
    <p class="contact__row">
      <svg viewBox="0 0 24 24" aria-hidden="true"><rect x="2" y="5" width="20" height="14" fill="var(--gold)"/><path d="M2 5l10 8 10-8" fill="none" stroke="var(--navy)" stroke-width="1.8"/></svg>
      hello@heronloans.com
    </p>
    <p class="contact__address">18 Harbor Lane, Suite 4<br>30215, Bayview</p>
  </div>

  <div class="band">www.heronloans.com</div>
</section>

</body>
</html>
```